Velmora Cabinets Letter Head and Email Signature

Hi
I would love a design package for a letterhead, email signature, even update my business card if you like if you can come up with a great idea for my new high end cabinet shop. Velmora Cabinets brings timeless craftsmanship to modern interiors, specializing in high end, custom cabinetry designed for architects and interior designers.

Target Market(s)

high end, luxury market

Industry/Entity Type

cabinet making

Requirements
Must have
• my colours of logo as the theme

```html
<!DOCTYPE html>
<html lang="en">
<head>
<meta charset="utf-8">
<title>Velmora Cabinets – Email Signature</title>
<link rel="stylesheet" href="https://fonts.googleapis.com/css2?family=Montserrat:wght@400;500;800&display=swap">
<style>
  :root {
    --page: #8a8a8a;
    --black: #000000;
    --panel-dark: #0a0a0a;
    --panel-light: #1a1a1a;
    --green: #4e7d4a;
    --white: #ffffff;
  }
  * { margin: 0; padding: 0; box-sizing: border-box; }
  html, body {
    width: 1200px;
    height: 610px;
    overflow: hidden;
    background: var(--page);
    font-family: "Montserrat", Arial, sans-serif;
  }
  .signature {
    position: absolute;
    left: 0;
    top: 105px;
    width: 1200px;
    height: 400px;
    background: var(--black);
    overflow: hidden;
  }
  .signature__shapes {
    position: absolute;
    inset: 0;
    width: 100%;
    height: 100%;
  }
  .person {
    position: absolute;
    left: 533px;
    top: 52px;
  }
  .person__name {
    color: var(--green);
    font-weight: 800;
    font-size: 43px;
    line-height: 1;
  }
  .person__role {
    margin-top: 12px;
    color: var(--white);
    font-weight: 500;
    font-size: 22px;
    letter-spacing: 3px;
    line-height: 1;
  }
  .brand {
    position: absolute;
    left: 80px;
    top: 232px;
    display: flex;
    align-items: center;
    gap: 22px;
  }
  .brand__mark {
    width: 60px;
    height: 60px;
    border: 4px solid var(--white);
  }
  .brand__name {
    color: var(--white);
    font-weight: 400;
    font-size: 34px;
    line-height: 1.05;
    letter-spacing: 2px;
  }
  .contacts {
    position: absolute;
    left: 533px;
    top: 218px;
    list-style: none;
  }
  .contacts__item {
    display: flex;
    align-items: center;
    gap: 12px;
    height: 42px;
    color: var(--white);
    font-weight: 500;
    font-size: 24px;
  }
  .contacts__icon {
    width: 20px;
    height: 20px;
    flex: none;
  }
</style>
</head>
<body>
  <section class="signature">
    <svg class="signature__shapes" viewBox="0 0 1081 360" preserveAspectRatio="none" aria-hidden="true">
      <defs>
        <linearGradient id="panelShade" x1="0" y1="0" x2="1" y2="0">
          <stop offset="0" stop-color="#060606"/>
          <stop offset="0.5" stop-color="#171717"/>
          <stop offset="1" stop-color="#161616"/>
        </linearGradient>
      </defs>
      <!-- lower contact panel -->
      <polygon points="0,158 1062,158 962,322 0,322 0,360 921,360 1081,360 0,360" fill="url(#panelShade)"/>
      <rect x="0" y="158" width="1050" height="202" fill="url(#panelShade)"/>
      <!-- top accent band -->
      <polygon points="378,0 1081,0 1081,22 366,22" fill="var(--green)"/>
      <!-- white angled rule -->
      <polygon points="94,90 314,90 364,0 380,0 323,104 94,104" fill="var(--white)"/>
      <!-- green angled rule -->
      <polygon points="1036,158 1055,158 954,338 722,338 722,322 944,322" fill="var(--green)"/>
      <!-- black wedge behind white corner -->
      <polygon points="1055,158 1081,158 1081,360 944,360" fill="var(--black)" opacity="0"/>
      <!-- white corner -->
      <polygon points="977,294 1081,294 1081,360 921,360" fill="var(--white)"/>
    </svg>

    <div class="person">
      <h1 class="person__name">Liam Harrow</h1>
      <p class="person__role">Director Craftsman</p>
    </div>

    <div class="brand">
      <span class="brand__mark"></span>
      <p class="brand__name">Velmora<br>Cabinets</p>
    </div>

    <ul class="contacts">
      <li class="contacts__item">
        <svg class="contacts__icon" viewBox="0 0 20 20" aria-hidden="true">
          <circle cx="10" cy="10" r="10" fill="var(--green)"/>
          <path d="M7 5.5l1.6 2.4-1 1a6 6 0 0 0 3.5 3.5l1-1 2.4 1.6-.8 1.6c-3.8.2-7.7-3.7-7.5-7.5z" fill="var(--white)"/>
        </svg>
        0400 318 562
      </li>
      <li class="contacts__item">
        <svg class="contacts__icon" viewBox="0 0 20 20" aria-hidden="true">
          <circle cx="10" cy="10" r="10" fill="var(--green)"/>
          <rect x="5" y="6.5" width="10" height="7" fill="var(--white)"/>
          <path d="M5 6.5l5 4 5-4" fill="none" stroke="var(--green)" stroke-width="1"/>
        </svg>
        liamh@velmoracabinets.com.au
      </li>
      <li class="contacts__item">
        <svg class="contacts__icon" viewBox="0 0 20 20" aria-hidden="true">
          <circle cx="10" cy="10" r="10" fill="var(--green)"/>
        </svg>
        @velmora.cabinets
      </li>
    </ul>
  </section>
</body>
</html>
```